Power Point Template Vierklang sustainability consulting

(find english description below)
We are a small German start-up that offers sustainability consulting. For presentations of results, our company presentation, proposals, lectures, etc., we need a PowerPoint template that matches our logo. We come from classic management consulting / strategy consulting and also deal with facts and figures in sustainability consulting. Therefore, the template should not be too fancy and should not only consist of photos. But it shouldn't be a completely sober template either. Our logo with the green leaves for sustainability (three leaves for VIERklang) and the white bar chart (with the dynamic swing upwards) reflects our attitude well, where we see ourselves on the range from playful to sober and classic to modern.

It might be nice for the template to include the shape of one of the leaves (from the logo). Also, the logo should appear in a corner of each slide. The colors from the logo (see appendix) should be partially reflected in the presentation. We can also imagine a gold-brown tone (see website www.vierklang-beratung.de) or a coral tone as a contrast. (Attention - the website is not final yet).

For a first suggestion, it is sufficient to suggest three to four slides (cover sheet, chapter/separation slide, text slide, data slide). We will then mark drafts that we like. In total, we would then need about 6-10 more slide templates, e.g. about us, team, slide for a statement, 2-3 data charts (pie, bar, column), top 3 - 5 list, timeline, contact (more slides are welcome ).

We are a small German start-up offering sustainability consulting. We need a power point template for result presentations, our company presentation, proposals, lectures etc. The template should be aligned with our logo. Our background lies in classic management consulting / strategy consulting and we also deal with facts and figures in sustainability consulting. Therefore, the template should not be too playful and not only consist of photos. But it should also not be a completely clear template. Our logo with the green leaves for sustainability (three leaves for VIERklang) and the white bar chart (with the dynamic upward swing) reflects our attitude well, where we see ourselves on the range from playful to down-to-earth and classic to modern .

For the template, it might be nice to incorporate the shape of one of the leaves (from the logo). Also, the logo should show up in one corner on each slide. Some of the colors from the logo (see attachment) should be reflected in the presentation. We could also think of a gold-brown tone (see website www.vierklang-beratung.de) or a coral tone for contrast. (Attention - the website is not final yet).

For a first proposal it is quite sufficient to suggest us three to four slides (cover page, chapter/separation slide, text slide, data slide). We will then mark the drafts that we like. In total we would need about 6-10 more slide templates, eg About us, Team, slide for a statement, 2-3 data charts (pie, bar, column), Top 3 - 5 List, Timeline, Contact (more slides are welcome).

Target Market(s)

Corporations, large companies and SMEs

Industry/Entity Type

Unternehmensberatung, Nachhaltigkeitsberatung

Font styles to use
Sans Serif
Other font styles liked:
• Calibri

Colors
00AB8E
00BBA5
67D7C9
C6EFE9
E9F9F6

Requirements
Must have
• see description (e.g. the colors of our logo)
Nice to have
• see description (e.g. elements of the logo included)
Should not have
• see description

```html
<!DOCTYPE html>
<html lang="en">
<head>
<meta charset="utf-8">
<title>Vierklang – Presentation Template Overview</title>
<link href="https://fonts.googleapis.com/css2?family=Jost:wght@300;400;500&display=swap" rel="stylesheet">
<style>
:root{
  --teal-deep:#00695c;
  --teal:#00AB8E;
  --teal-bright:#00BBA5;
  --teal-soft:#67D7C9;
  --teal-mist:#C6EFE9;
  --teal-pale:#E9F9F6;
  --orange:#df8149;
  --gold:#c08a4e;
  --coral:#e8502f;
  --ink:#555;
  --muted:#9a9a9a;
  --rule:#e6e6e6;
}
*{box-sizing:border-box;margin:0;padding:0}
html,body{width:1200px;height:1200px;overflow:hidden;background:#fff}
.canvas{position:relative;width:1200px;height:1200px;background:#fff;font-family:"Jost",sans-serif}

.slide{position:absolute;width:516px;height:290px;transform:scale(.5);transform-origin:0 0;background:#fff;
  box-shadow:0 6px 22px rgba(0,0,0,.28);overflow:hidden;color:var(--ink)}
.slide > *{position:absolute}

.rail{left:0;top:0;bottom:0;width:26px;border-right:1px solid var(--rule)}
.rail.right{left:auto;right:0;border-right:0;border-left:1px solid var(--rule)}
.rail .dot{position:absolute;top:8px;left:6px;width:14px;height:14px;border-radius:50%;background:var(--teal)}
.rail .url{position:absolute;left:8px;bottom:40px;writing-mode:vertical-rl;transform:rotate(180deg);font-size:6px;color:var(--teal);letter-spacing:.2px}
.rail .num{position:absolute;left:0;bottom:0;width:26px;height:22px;background:var(--coral);color:#fff;font-size:6px;display:flex;align-items:center;justify-content:center}

.kicker{font-size:5.5px;color:#777}
.title{font-size:16px;font-weight:300;color:var(--orange);line-height:1.15}
.title.center{left:26px;right:0;text-align:center}
.sub{font-size:6px;color:var(--gold);line-height:1.3}
.copy{font-size:5px;color:#666;line-height:1.45;text-align:justify}
.copy.gold{color:var(--gold)}
.copy.center{text-align:center}
.footer{font-size:6px;color:var(--muted);right:26px;bottom:8px}
.ruled{border-left:1px solid #777;padding-left:8px}

.ph{display:block}
.ph.forest{background:linear-gradient(140deg,#003f37 0%,#00806c 45%,#67D7C9 75%,#E9F9F6 100%)}
.ph.office{background:linear-gradient(135deg,#ecebe8 0%,#a9a7a2 45%,#3a3a3e 100%)}
.ph.mountain{background:linear-gradient(180deg,#f3ead4 0%,#C6EFE9 40%,#5fb6a6 72%,#1f6c60 100%)}
.ph.people{background:linear-gradient(180deg,#d7d7d5 0%,#9c9c9a 50%,#2c2c30 100%)}
.ph.portrait{border-radius:50%;background:radial-gradient(circle at 50% 40%,#d9c7b8 0%,#9a8a80 55%,#dcdcdc 100%)}
.shadowed{box-shadow:0 3px 8px rgba(0,0,0,.18)}

.ico{width:24px;height:24px;border-radius:50%;background:var(--teal);display:flex;align-items:center;justify-content:center}
.ico svg{width:12px;height:12px}

.toc h4{font-weight:400;font-size:6px;color:var(--gold);margin-bottom:5px}
.toc li{list-style:none;font-size:5px;color:#555;display:flex;justify-content:space-between;margin-bottom:4px}
.toc li span:last-child{color:var(--muted)}

.brand{font-weight:400;color:var(--teal)}
.tiny{font-size:4.5px;color:var(--muted)}
.bullets p{font-size:4.8px;color:#666;line-height:1.45;text-align:justify;padding-left:6px;position:relative;margin-bottom:4px}
.bullets p::before{content:"";position:absolute;left:0;top:2px;width:2.5px;height:2.5px;border-radius:50%;background:var(--teal)}
</style>
</head>
<body>
<div class="canvas">

<!-- 1 Cover -->
<section class="slide" style="left:33.5px;top:60px">
  <div class="ph" style="left:0;top:27px;width:488px;height:236px;background:linear-gradient(135deg,#e99261 0%,#dd7a44 55%,#d06a36 100%)" role="img" aria-label="Warm-toned forest photograph behind the cover title"></div>
  <div class="brand" style="left:40px;top:138px;font-size:34px;color:#fff;font-weight:300">Vierklang</div>
  <div style="left:78px;top:178px;font-size:7px;color:#fff;letter-spacing:.5px">CONSULTING</div>
  <div style="left:212px;top:56px;width:240px;font-size:24px;font-weight:300;color:#fff;line-height:1.05">PLACE HERE YOUR TITLE PRESENTATION</div>
  <div style="left:212px;top:168px;font-size:7.5px;color:#fbe3d3">Your Subtitle Presentation goes here</div>
  <div style="left:212px;top:210px;font-size:4.5px;color:#fbe3d3;line-height:1.5">Prepared by: Jane Doe · Managing Partner<br>Frankfurt, 01.01.2025</div>
  <div class="footer">Visit us | www.vierklang-beratung.de</div>
</section>

<!-- 2 Welcome -->
<section class="slide" style="left:325px;top:60px">
  <div class="brand" style="left:36px;top:26px;font-size:18px">Vierklang</div>
  <div style="left:104px;top:48px;font-size:4.5px;color:#555">CONSULTING</div>
  <div class="title" style="left:34px;top:148px;font-size:20px">Welcome,</div>
  <div style="left:34px;top:180px;width:230px;font-size:8.5px;color:#333;line-height:2.1">Lorem Ipsum is simply dummy text of the printing and typesetting industry.</div>
  <div style="left:320px;top:46px;width:140px;height:140px;border-radius:50%;background:linear-gradient(135deg,var(--teal-deep) 0%,var(--teal) 50%,var(--teal-soft) 100%)"></div>
  <div class="brand" style="left:338px;top:196px;font-size:22px;font-weight:300">Vierklang</div>
  <div style="left:10px;bottom:8px;font-size:5px;color:var(--muted)">2</div>
  <div class="footer">Visit us | www.vierklang-beratung.de</div>
</section>

<!-- 3 Table of content -->
<section class="slide" style="left:613px;top:60px">
  <div class="rail right"><span class="dot"></span><span class="url">www.vierklang-beratung.de</span><span class="num">3</span></div>
  <div class="kicker" style="left:64px;top:42px">Welcome</div>
  <div class="title" style="left:64px;top:52px;font-size:12px">Table of Content</div>
  <div class="copy ruled" style="left:64px;top:82px;width:360px">Lorem Ipsum is simply dummy text of the printing and typesetting industry. Lorem Ipsum has been the industry's standard dummy text ever since the 1500s, when an unknown printer took a galley of type.</div>
  <div class="toc" style="left:64px;top:130px;width:110px"><h4>About Us</h4><ul><li><span>01.1 About Us</span><span>03</span></li><li><span>01.2 Our Team</span><span>04</span></li><li><span>01.3 Facts</span><span>05</span></li></ul></div>
  <div class="toc" style="left:183px;top:130px;width:110px"><h4>Section two description</h4><ul><li><span>02.1 What is the Method?</span><span>06</span></li><li><span>02.2 What we do</span><span>07</span></li><li><span>02.3 Certified</span><span>08</span></li></ul></div>
  <div class="toc" style="left:302px;top:130px;width:110px"><h4>Section three description</h4><ul><li><span>03.1 What is Vierklang?</span><span>09</span></li><li><span>03.2 Why Us</span><span>10</span></li><li><span>03.3 Our experience</span><span>11</span></li></ul></div>
  <div class="toc" style="left:64px;top:190px;width:110px"><h4>Section Four description</h4><ul><li><span>04.1 Introduction</span><span>12</span></li><li><span>04.2 Corporate Colors</span><span>13</span></li><li><span>04.3 Color Scheme</span><span>14</span></li></ul></div>
  <div class="toc" style="left:183px;top:190px;width:110px"><h4>Section Five description</h4><ul><li><span>05.1 Print System</span><span>15</span></li><li><span>05.2 Web System</span><span>16</span></li><li><span>05.3 Corporate Images</span><span>17</span></li></ul></div>
  <div class="toc" style="left:302px;top:190px;width:110px"><h4>Section Six description</h4><ul><li><span>06.1 Introduction</span><span>18</span></li><li><span>06.2 Icon Application</span><span>19</span></li><li><span>06.3 Infographic System</span><span>20</span></li></ul></div>
</section>

<!-- 4 Company intro -->
<section class="slide" style="left:906px;top:60px">
  <div class="rail right"><span class="dot"></span><span class="url">www.vierklang-beratung.de</span><span class="num">4</span></div>
  <div class="ph people" style="left:27px;top:38px;width:274px;height:206px" role="img" aria-label="Photograph of three team members standing in business attire"></div>
  <div class="kicker" style="left:324px;top:52px">Company Introduction</div>
  <div class="title" style="left:324px;top:62px;font-size:13px">Our Company Intro</div>
  <div class="sub" style="left:324px;top:80px">Welcome to the best Company.</div>
  <div class="copy gold" style="left:324px;top:96px;width:150px;opacity:.75">Lorem Ipsum is simply dummy text of the printing and typesetting industry. Lorem Ipsum has been the industry's standard dummy text ever since the 1500s, when an unknown printer took a galley of type and scrambled it to make a type specimen book. It has survived not only five centuries, but also the leap into electronic typesetting, remaining essentially unchanged.</div>
</section>

<!-- 5 Brand guidelines -->
<section class="slide" style="left:33.5px;top:247px">
  <div class="rail"><span class="dot"></span><span class="url">www.vierklang-beratung.de</span><span class="num">5</span></div>
  <div class="kicker" style="left:64px;top:50px">Brand Guideline Introduction</div>
  <div class="title" style="left:64px;top:60px;font-size:12px">Our Brand Guidelines</div>
  <div class="copy ruled" style="left:64px;top:96px;width:190px">Lorem Ipsum is simply dummy text of the printing and typesetting industry. Lorem Ipsum has been the industry's standard dummy text ever since the 1500s, when an unknown printer took a galley of type.</div>
  <div class="ico" style="left:66px;top:166px"><svg viewBox="0 0 12 12"><path d="M2 10l1-3 5-5 2 2-5 5z" fill="none" stroke="#fff" stroke-width="1"/></svg></div>
  <div class="ico" style="left:184px;top:166px"><svg viewBox="0 0 12 12"><rect x="3" y="2" width="6" height="8" fill="none" stroke="#fff" stroke-width="1"/><path d="M4.5 5h3M4.5 7h3" stroke="#fff" stroke-width=".8"/></svg></div>
  <div class="sub" style="left:58px;top:204px">Your subtitle slide here.</div>
  <div class="copy" style="left:58px;top:214px;width:80px">Lorem Ipsum is simply dummy text of the printing and typesetting industry.</div>
  <div class="sub" style="left:176px;top:204px">Your subtitle slide here.</div>
  <div class="copy" style="left:176px;top:214px;width:80px">Lorem Ipsum is simply dummy text of the printing and typesetting industry.</div>
  <div class="ph forest" style="left:302px;top:27px;width:188px;height:237px" role="img" aria-label="Sunlit forest photograph"></div>
</section>

<!-- 6 Branding values -->
<section class="slide" style="left:325px;top:247px">
  <div class="rail right"><span class="dot"></span><span class="url">www.vierklang-beratung.de</span><span class="num">6</span></div>
  <div class="shadowed" style="left:27px;top:27px;width:138px;height:236px;background:#fff"></div>
  <div class="shadowed" style="left:178px;top:27px;width:138px;height:236px;background:#fff"></div>
  <div class="ph office" style="left:27px;top:27px;width:138px;height:176px" role="img" aria-label="Photograph of hands writing in a notebook"></div>
  <div class="ph office" style="left:178px;top:27px;width:138px;height:176px" role="img" aria-label="Photograph of a consultant working at a laptop"></div>
  <div class="copy" style="left:34px;top:212px;width:120px">Lorem Ipsum is simply dummy text of the printing and typesetting industry. Lorem Ipsum has been the industry's standard.</div>
  <div class="copy" style="left:185px;top:212px;width:120px">Lorem Ipsum is simply dummy text of the printing and typesetting industry. Lorem Ipsum has been the industry's standard.</div>
  <div class="kicker" style="left:332px;top:36px">Lorem Ipsum is simply dummy text of the</div>
  <div class="title" style="left:332px;top:46px;font-size:12px;width:150px">Branding Values and Reputation</div>
  <div class="sub" style="left:332px;top:88px">Lorem Ipsum is simply dummy text</div>
  <div class="copy" style="left:332px;top:106px;width:150px">Lorem Ipsum is simply dummy text of the printing and typesetting industry. Lorem Ipsum has been the industry's standard dummy text ever since the 1500s, when an unknown printer took a galley of type and scrambled it to make a type specimen book. It has survived not only five centuries, but also the leap into electronic typesetting.</div>
  <div class="copy gold" style="left:332px;top:196px;width:150px">Lorem Ipsum is simply dummy text of the printing and typesetting industry.</div>
  <div style="left:332px;top:256px;width:130px;height:3px;background:linear-gradient(90deg,var(--teal-deep),var(--teal-soft))"></div>
</section>

<!-- 7 Company values -->
<section class="slide" style="left:613px;top:247px">
  <div class="rail"><span class="dot"></span><span class="url">www.vierklang-beratung.de</span><span class="num">7</span></div>
  <div class="kicker" style="left:62px;top:44px">Company Values</div>
  <div class="title" style="left:62px;top:54px;font-size:12px;width:160px">Company Values and Strengths</div>
  <div class="copy gold" style="left:62px;top:98px;width:150px">Lorem Ipsum is simply dummy text of the printing and typesetting industry. Lorem Ipsum has been the industry's standard dummy text ever since the 1500s.</div>
  <div class="copy" style="left:62px;top:146px;width:150px">When an unknown printer took a galley of type and scrambled it to make a type specimen book. It has survived not only five centuries, but also the leap into electronic typesetting, remaining essentially unchanged. It was popularised in the 1960s with the release of Letraset sheets containing Lorem Ipsum passages.</div>
  <div class="sub" style="left:258px;top:44px">Our Identity</div>
  <div class="sub" style="left:338px;top:44px">Our Values</div>
  <div class="sub" style="left:418px;top:44px">Our Philosophy</div>
  <div class="ph people" style="left:258px;top:56px;width:70px;height:52px" role="img" aria-label="Photograph of the team"></div>
  <div class="ph office" style="left:338px;top:56px;width:70px;height:52px" role="img" aria-label="Photograph of a meeting"></div>
  <div class="ph office" style="left:418px;top:56px;width:70px;height:52px" role="img" aria-label="Photograph of a workspace"></div>
  <div class="copy" style="left:258px;top:120px;width:70px">Lorem Ipsum is simply dummy text of the printing and typesetting industry. Lorem Ipsum has been the industry's standard dummy text ever since the 1500s.</div>
  <div class="copy" style="left:338px;top:120px;width:70px">Lorem Ipsum is simply dummy text of the printing and typesetting industry. Lorem Ipsum has been the industry's standard dummy text ever since the 1500s.</div>
  <div class="copy" style="left:418px;top:120px;width:70px">Lorem Ipsum is simply dummy text of the printing and typesetting industry. Lorem Ipsum has been the industry's standard dummy text ever since the 1500s.</div>
</section>

<!-- 8 Section break -->
<section class="slide" style="left:906px;top:247px">
  <div class="ph forest" style="left:0;top:0;width:516px;height:290px" role="img" aria-label="Forest photograph with sun rays"></div>
  <svg style="left:0;top:0" width="516" height="290" viewBox="0 0 516 290"><path d="M0 290 C120 240 300 250 516 196 L516 290 Z" fill="#fff"/></svg>
  <div style="left:0;right:0;top:136px;text-align:center;font-size:28px;font-weight:300;color:#fff">BRAKE SECTION SLIDE</div>
  <div style="left:0;right:0;top:180px;text-align:center;font-size:7px;color:#fff">Lorem Ipsum is simply dummy text of the printing and typesetting</div>
  <div style="left:410px;top:259px;width:9px;height:9px;border-radius:50%;background:var(--teal)"></div>
  <div class="brand" style="left:423px;top:253px;font-size:13px">Vierklang</div>
</section>

<!-- 9 About products -->
<section class="slide" style="left:33.5px;top:434px">
  <div class="rail"><span class="dot"></span><span class="url">www.vierklang-beratung.de</span><span class="num">9</span></div>
  <div class="kicker" style="left:64px;top:28px;color:var(--gold)">Lorem ipsum is simply dummy</div>
  <div class="title" style="left:64px;top:46px;font-size:12px">About Our Products</div>
  <div class="ph office" style="left:64px;top:78px;width:200px;height:130px" role="img" aria-label="Photograph of hands writing in a notebook"></div>
  <div class="sub" style="left:312px;top:76px">Your subtitle slide here.</div>
  <div class="copy" style="left:312px;top:86px;width:150px">Lorem Ipsum is simply dummy text of the printing and typesetting industry. Lorem Ipsum has been the industry's standard dummy text ever since the 1500s.</div>
  <div class="sub" style="left:312px;top:122px">Your subtitle slide here.</div>
  <div class="copy" style="left:312px;top:132px;width:150px">Lorem Ipsum is simply dummy text of the printing and typesetting industry. Lorem Ipsum has been the industry's standard dummy text ever since the 1500s.</div>
  <div class="sub" style="left:312px;top:170px">Your subtitle slide here.</div>
  <div class="copy" style="left:312px;top:180px;width:150px">Lorem Ipsum is simply dummy text of the printing and typesetting industry. Lorem Ipsum has been the industry's standard dummy text ever since the 1500s.</div>
  <div class="sub" style="left:64px;top:222px">Your subtitle slide here</div>
  <div class="copy" style="left:64px;top:232px;width:400px">When an unknown printer took a galley of type and scrambled it to make a type specimen book. It has survived not only five centuries, but also the leap into electronic typesetting, remaining essentially unchanged. It was popularised in the 1960s with the release of Letraset sheets.</div>
</section>

<!-- 10 Section break -->
<section class="slide" style="left:325px;top:434px">
  <div class="ph" style="left:0;top:0;width:516px;height:290px;background:linear-gradient(115deg,#efe3c8 0%,#9fd6cb 30%,#2b8a7a 50%,#0b3f38 70%,#00AB8E 100%)" role="img" aria-label="Misty mountain landscape and forest foliage photograph"></div>
  <div class="brand" style="left:40px;top:40px;font-size:14px;color:#fff">Vierklang</div>
  <div style="left:0;right:0;top:136px;text-align:center;font-size:28px;font-weight:300;color:#fff">BRAKE SECTION SLIDE</div>
  <div style="left:10px;bottom:8px;font-size:5px;color:#fff">10</div>
</section>

<!-- 11 Bullets -->
<section class="slide" style="left:613px;top:434px">
  <div class="rail"><span class="dot"></span><span class="url">www.vierklang-beratung.de</span><span class="num">11</span></div>
  <div class="title center" style="top:22px;font-size:12px">Click here to your title Bullets slide</div>
  <div class="ico" style="left:138px;top:62px"><svg viewBox="0 0 12 12"><path d="M6 11s3.5-3.6 3.5-6A3.5 3.5 0 0 0 2.5 5c0 2.4 3.5 6 3.5 6z" fill="none" stroke="#fff"/></svg></div>
  <div class="ico" style="left:292px;top:62px"><svg viewBox="0 0 12 12"><circle cx="6" cy="6.5" r="4" fill="none" stroke="#fff"/><path d="M6 4.5v2l1.4 1" stroke="#fff" fill="none"/></svg></div>
  <div class="ico" style="left:446px;top:62px"><svg viewBox="0 0 12 12"><circle cx="5" cy="5" r="3" fill="none" stroke="#fff"/><path d="M7.2 7.2L10.5 10.5" stroke="#fff"/></svg></div>
  <div class="ico" style="left:138px;top:162px"><svg viewBox="0 0 12 12"><circle cx="6" cy="6" r="4.5" fill="none" stroke="#fff"/><circle cx="6" cy="6" r="2.2" fill="none" stroke="#fff"/><circle cx="6" cy="6" r=".8" fill="#fff"/></svg></div>
  <div class="ico" style="left:292px;top:162px"><svg viewBox="0 0 12 12"><circle cx="6" cy="4.5" r="2.5" fill="none" stroke="#fff"/><path d="M4.5 7l-1 4 2.5-1.5 2.5 1.5-1-4" fill="none" stroke="#fff"/></svg></div>
  <div class="ico" style="left:446px;top:162px"><svg viewBox="0 0 12 12"><circle cx="6" cy="4" r="2.2" fill="#fff"/><path d="M2 11a4 4 0 0 1 8 0z" fill="#fff"/></svg></div>
  <div class="copy center" style="left:95px;top:94px;width:110px;color:var(--gold)">Consultancy</div>
  <div class="copy center" style="left:95px;top:104px;width:110px">Lorem ipsum randomised words which don't look even slightly believable in some form.</div>
  <div class="copy center" style="left:249px;top:94px;width:110px;color:var(--gold)">Consultancy</div>
  <div class="copy center" style="left:249px;top:104px;width:110px">Lorem ipsum randomised words which don't look even slightly believable in some form.</div>
  <div class="copy center" style="left:403px;top:94px;width:110px;color:var(--gold)">Consultancy</div>
  <div class="copy center" style="left:403px;top:104px;width:110px">Lorem ipsum randomised words which don't look even slightly believable in some form.</div>
  <div class="copy center" style="left:95px;top:194px;width:110px;color:var(--gold)">Consultancy</div>
  <div class="copy center" style="left:95px;top:204px;width:110px">Lorem ipsum randomised words which don't look even slightly believable in some form.</div>
  <div class="copy center" style="left:249px;top:194px;width:110px;color:var(--gold)">Consultancy</div>
  <div class="copy center" style="left:249px;top:204px;width:110px">Lorem ipsum randomised words which don't look even slightly believable in some form.</div>
  <div class="copy center" style="left:403px;top:194px;width:110px;color:var(--gold)">Consultancy</div>
  <div class="copy center" style="left:403px;top:204px;width:110px">Lorem ipsum randomised words which don't look even slightly believable in some form.</div>
</section>

<!-- 12 Team -->
<section class="slide" style="left:906px;top:434px">
  <div class="rail"><span class="dot"></span><span class="url">www.vierklang-beratung.de</span><span class="num">12</span></div>
  <div class="title center" style="top:22px;font-size:14px">Meet our Team</div>
  <div class="ph portrait" style="left:88px;top:88px;width:64px;height:64px" role="img" aria-label="Portrait of a partner"></div>
  <div class="ph portrait" style="left:236px;top:88px;width:64px;height:64px" role="img" aria-label="Portrait of a partner"></div>
  <div class="ph portrait" style="left:384px;top:88px;width:64px;height:64px" role="img" aria-label="Portrait of a partner"></div>
  <div class="copy center" style="left:80px;top:162px;width:80px;color:var(--gold)">Partner name</div>
  <div class="copy center" style="left:228px;top:162px;width:80px;color:var(--gold)">Partner name</div>
  <div class="copy center" style="left:376px;top:162px;width:80px;color:var(--gold)">Partner name</div>
  <div class="tiny" style="left:80px;top:172px;width:80px;text-align:center">Job position here</div>
  <div class="tiny" style="left:228px;top:172px;width:80px;text-align:center">Job position here</div>
  <div class="tiny" style="left:376px;top:172px;width:80px;text-align:center">Job position here</div>
  <div class="copy" style="left:80px;top:184px;width:80px">When an unknown printer took a galley of type and scrambled it to make a type specimen book. It has survived not only five centuries.</div>
  <div class="copy" style="left:228px;top:184px;width:80px">When an unknown printer took a galley of type and scrambled it to make a type specimen book. It has survived not only five centuries.</div>
  <div class="copy" style="left:376px;top:184px;width:80px">When an unknown printer took a galley of type and scrambled it to make a type specimen book. It has survived not only five centuries.</div>
</section>

<!-- 13 Product background -->
<section class="slide" style="left:33.5px;top:620px">
  <div class="rail"><span class="dot"></span><span class="url">www.vierklang-beratung.de</span><span class="num">13</span></div>
  <div class="kicker" style="left:64px;top:46px">Lorem ipsum is simply dummy text</div>
  <div class="title" style="left:64px;top:56px;font-size:12px">How our Product Works Background</div>
  <div class="copy" style="left:64px;top:80px;width:250px">Lorem Ipsum is simply dummy text of the printing and typesetting industry. Lorem Ipsum has been the industry's standard dummy text ever since the 1500s, when an unknown printer took a galley of type and scrambled it to make a type specimen book. It has survived not only five centuries, but also the leap into electronic typesetting, remaining essentially unchanged. It was popularised in the 1960s with the release of Letraset sheets.</div>
  <div class="copy" style="left:64px;top:146px;width:250px">We want to see more charts translating our vision of having a market leading platform. Digitalize in this space to provide 360 degree content. If people believe they share values with a company, they will stay loyal to the brand.</div>
  <div style="left:64px;top:190px;width:12px;height:12px;border-radius:50%;background:var(--teal)"></div>
  <div style="left:144px;top:190px;width:12px;height:12px;border-radius:50%;background:var(--teal)"></div>
  <div style="left:224px;top:190px;width:12px;height:12px;border-radius:50%;background:var(--teal)"></div>
  <div class="copy" style="left:80px;top:190px;width:56px;text-align:left">Lorem Ipsum is simply dummy text of the printing and typesetting industry.</div>
  <div class="copy" style="left:160px;top:190px;width:56px;text-align:left">Lorem Ipsum is simply dummy text of the printing and typesetting industry.</div>
  <div class="copy" style="left:240px;top:190px;width:56px;text-align:left">Lorem Ipsum is simply dummy text of the printing and typesetting industry.</div>
  <div class="ph mountain" style="left:342px;top:30px;width:148px;height:62px" role="img" aria-label="Misty mountains photograph"></div>
  <div class="ph forest" style="left:342px;top:102px;width:148px;height:78px" role="img" aria-label="Forest light photograph"></div>
  <div class="ph" style="left:342px;top:192px;width:148px;height:98px;background:linear-gradient(135deg,#0b3f38,#2b9a86,#d8e6d0)" role="img" aria-label="Green fruit on a branch photograph"></div>
</section>

<!-- 14 Product background two photos -->
<section class="slide" style="left:325px;top:620px">
  <div class="rail"><span class="dot"></span><span class="url">www.vierklang-beratung.de</span><span class="num">14</span></div>
  <div class="kicker" style="left:62px;top:36px">Lorem ipsum is simply dummy text</div>
  <div class="title" style="left:62px;top:46px;font-size:12px;width:150px">How our Product Works Background</div>
  <div class="copy" style="left:62px;top:84px;width:196px">Lorem Ipsum is simply dummy text of the printing and typesetting industry. Lorem Ipsum has been the industry's standard dummy text ever since the 1500s, when an unknown printer took a galley of type and scrambled it to make a type specimen book. It has survived not only five centuries, but also the leap into electronic typesetting, remaining essentially unchanged.</div>
  <div class="copy" style="left:62px;top:150px;width:196px">When an unknown printer took a galley of type and scrambled it to make a type specimen book. It has survived not only five centuries, but also the leap into electronic typesetting, remaining essentially unchanged. It was popularised in the 1960s with the release of Letraset sheets containing Lorem Ipsum passages, and more recently with desktop publishing software.</div>
  <div class="ph office" style="left:282px;top:38px;width:206px;height:96px" role="img" aria-label="Photograph of hands writing in a notebook"></div>
  <div class="ph office" style="left:282px;top:148px;width:206px;height:102px" role="img" aria-label="Photograph of two consultants in a meeting"></div>
</section>

<!-- 15 Text and three images -->
<section class="slide" style="left:613px;top:620px">
  <div class="rail"><span class="dot"></span><span class="url">www.vierklang-beratung.de</span><span class="num">15</span></div>
  <div style="left:62px;top:50px;width:150px;height:1.5px;background:var(--teal)"></div>
  <div class="kicker" style="left:62px;top:62px">Image System</div>
  <div class="title" style="left:62px;top:72px;font-size:12px">Text Slide &amp; Three Images</div>
  <div class="copy" style="left:62px;top:98px;width:186px">Lorem Ipsum is simply dummy text of the printing and typesetting industry. Lorem Ipsum has been the industry's standard dummy text ever since the 1500s, when an unknown printer took a galley of type and scrambled it to make a type specimen book. It has survived not only five centuries, but also the leap into electronic typesetting, remaining essentially unchanged. It was popularised in the 1960s with the release of Letraset sheets containing Lorem Ipsum passages, and more recently with desktop publishing software.</div>
  <div class="copy gold" style="left:62px;top:194px;width:186px">Lorem Ipsum is simply dummy text of the printing</div>
  <div class="copy" style="left:62px;top:204px;width:186px">And typesetting. When an unknown printer took a galley of type and scrambled it to make a type specimen book.</div>
  <div class="ph office" style="left:262px;top:48px;width:110px;height:216px" role="img" aria-label="Photograph of a consultant reading documents"></div>
  <div class="ph forest" style="left:378px;top:48px;width:110px;height:92px" role="img" aria-label="Green leaves photograph"></div>
  <div class="ph mountain" style="left:378px;top:148px;width:110px;height:116px" role="img" aria-label="Misty mountains photograph"></div>
</section>

<!-- 16 Three columns with images -->
<section class="slide" style="left:906px;top:620px">
  <div class="rail"><span class="dot"></span><span class="url">www.vierklang-beratung.de</span><span class="num">16</span></div>
  <div class="title center" style="top:28px;font-size:17px">Click to edit title slide</div>
  <div class="tiny" style="left:26px;right:0;top:56px;text-align:center;font-size:4px">LOREM IPSUM, GIVING INFORMATION ON ITS ORIGINS, AS WELL AS A RANDOM TEXT HERE</div>
  <div class="sub" style="left:50px;top:88px;width:126px;text-align:center;font-size:8px">Lorem dummy text</div>
  <div class="sub" style="left:197px;top:88px;width:126px;text-align:center;font-size:8px">Lorem dummy text</div>
  <div class="sub" style="left:344px;top:88px;width:126px;text-align:center;font-size:8px">Lorem dummy text</div>
  <div class="ph mountain" style="left:50px;top:112px;width:126px;height:72px" role="img" aria-label="Mountain landscape photograph"></div>
  <div class="ph office" style="left:197px;top:112px;width:126px;height:72px" role="img" aria-label="Photograph of hands writing"></div>
  <div class="ph office" style="left:344px;top:112px;width:126px;height:72px" role="img" aria-label="Photograph of a team meeting"></div>
  <div style="left:50px;top:202px;width:126px;font-size:6px;color:#555;line-height:1.6">Lorem Ipsum is simply dummy text of the printing and typesetting industry. Lorem Ipsum has been the.</div>
  <div style="left:197px;top:202px;width:126px;font-size:6px;color:#555;line-height:1.6">Lorem Ipsum is simply dummy text of the printing and typesetting industry. Lorem Ipsum has been the.</div>
  <div style="left:344px;top:202px;width:126px;font-size:6px;color:#555;line-height:1.6">Lorem Ipsum is simply dummy text of the printing and typesetting industry. Lorem Ipsum has been the.</div>
</section>

<!-- 17 Feature timeline -->
<section class="slide" style="left:33.5px;top:808px">
  <div class="rail"><span class="dot"></span><span class="url">www.vierklang-beratung.de</span><span class="num">17</span></div>
  <div class="title center" style="top:40px;font-size:17px">Your Title Text Goes Here</div>
  <svg style="left:0;top:0" width="516" height="290" viewBox="0 0 516 290">
    <path d="M26 176 C60 110 100 150 120 166 S 160 210 196 166 S 250 120 274 166 S 330 210 350 166 S 400 120 430 166 S 480 200 516 150" fill="none" stroke="#ddd" stroke-width="1.2"/>
    <g fill="none" stroke-width="3">
      <circle cx="136" cy="166" r="30" stroke="#e3e3e3"/><path d="M136 196 A30 30 0 0 1 106 166" stroke="#00695c"/>
      <circle cx="212" cy="166" r="30" stroke="#e3e3e3"/><path d="M182 166 A30 30 0 0 1 212 136" stroke="#555"/>
      <circle cx="288" cy="166" r="30" stroke="#e3e3e3"/><path d="M288 196 A30 30 0 0 1 258 166" stroke="#00AB8E"/>
      <circle cx="364" cy="166" r="30" stroke="#e3e3e3"/><path d="M364 136 A30 30 0 0 1 394 166" stroke="#67D7C9"/>
    </g>
    <g fill="#fff" style="filter:drop-shadow(0 2px 3px rgba(0,0,0,.2))">
      <circle cx="136" cy="166" r="22"/><circle cx="212" cy="166" r="22"/><circle cx="288" cy="166" r="22"/><circle cx="364" cy="166" r="22"/>
    </g>
    <g fill="none" stroke="#555" stroke-width="1.2">
      <rect x="127" y="158" width="14" height="11"/><rect x="135" y="164" width="9" height="9" fill="#fff" stroke="#00AB8E"/>
      <circle cx="212" cy="160" r="4"/><path d="M204 176 a8 8 0 0 1 16 0"/>
      <rect x="280" y="162" width="16" height="10" rx="2"/><path d="M284 162 v-4 h8 v4"/>
      <path d="M356 174 l16 -16 -5 16 -3 -6 z"/>
    </g>
    <g font-family="Jost, sans-serif" font-size="5" fill="#999" text-anchor="middle">
      <text x="212" y="126">2005</text><text x="364" y="126" fill="#00BBA5">2010</text>
      <text x="136" y="210">1990</text><text x="288" y="210">2020</text>
    </g>
  </svg>
  <div class="copy center" style="left:96px;top:90px;width:80px;color:#555;font-size:6px">Feature title one</div>
  <div class="tiny" style="left:96px;top:100px;width:80px;text-align:center">Lorem ipsum dolor sit amet, consectetuer</div>
  <div class="copy center" style="left:248px;top:90px;width:80px;color:#555;font-size:6px">Feature title one</div>
  <div class="tiny" style="left:248px;top:100px;width:80px;text-align:center">Lorem ipsum dolor sit amet, consectetuer</div>
  <div class="copy center" style="left:172px;top:216px;width:80px;color:#555;font-size:6px">Feature title one</div>
  <div class="tiny" style="left:172px;top:226px;width:80px;text-align:center">Lorem ipsum dolor sit amet, consectetuer</div>
  <div class="copy center" style="left:324px;top:216px;width:80px;color:#555;font-size:6px">Feature title one</div>
  <div class="tiny" style="left:324px;top:226px;width:80px;text-align:center">Lorem ipsum dolor sit amet, consectetuer</div>
</section>

<!-- 18 Year timeline -->
<section class="slide" style="left:325px;top:808px">
  <div class="rail"><span class="dot"></span><span class="url">www.vierklang-beratung.de</span><span class="num">18</span></div>
  <div class="title center" style="top:38px;font-size:17px">Your Title Text Goes Here</div>
  <div class="copy center" style="left:80px;top:70px;width:380px">Lorem ipsum dolor sit amet, consectetuer adipiscing elit. Aenean commodo ligula eget dolor. Aenean massa. Cum sociis natoque penatibus et magnis dis parturient montes, nascetur ridiculus mus.</div>
  <svg style="left:0;top:0" width="516" height="290" viewBox="0 0 516 290">
    <g fill="#fff" stroke-width="7">
      <circle cx="100" cy="172" r="30" stroke="#4fb8a8"/>
      <circle cx="167" cy="172" r="30" stroke="#00574d"/>
      <circle cx="234" cy="172" r="30" stroke="#00897a"/>
      <circle cx="301" cy="172" r="30" stroke="#67D7C9"/>
      <circle cx="367" cy="172" r="30" stroke="#8a8a8a"/>
      <circle cx="434" cy="172" r="30" stroke="#555"/>
    </g>
    <g font-family="Jost, sans-serif" font-size="13" font-weight="300" fill="#333" text-anchor="middle">
      <text x="100" y="177">1992</text><text x="167" y="177">1995</text><text x="234" y="177">2000</text>
      <text x="301" y="177">2007</text><text x="367" y="177">2016</text><text x="434" y="177">2022</text>
    </g>
  </svg>
  <div class="tiny" style="left:70px;top:118px;width:60px;text-align:center;color:#777">Amazing history content</div>
  <div class="tiny" style="left:204px;top:118px;width:60px;text-align:center;color:#777">Amazing history content</div>
  <div class="tiny" style="left:337px;top:118px;width:60px;text-align:center;color:#777">Amazing history content</div>
  <div class="tiny" style="left:137px;top:214px;width:60px;text-align:center;color:#777">Amazing history content</div>
  <div class="tiny" style="left:271px;top:214px;width:60px;text-align:center;color:#777">Amazing history content</div>
  <div class="tiny" style="left:404px;top:214px;width:60px;text-align:center;color:#777">Amazing history content</div>
</section>

<!-- 19 Two column text -->
<section class="slide" style="left:613px;top:808px">
  <div class="rail"><span class="dot"></span><span class="url">www.vierklang-beratung.de</span><span class="num">19</span></div>
  <div class="title center" style="top:18px;font-size:17px">Two Column Text Slide</div>
  <div class="bullets" style="left:50px;top:52px;width:205px">
    <p>Lorem ipsum dolor sit amet, consectetur adipiscing elit. Nulla sit amet urna sagittis, maximus orci eget, sodales nibh. Duis eu purus gravida, dignissim eros posuere, ornare nisi. Pellentesque habitant morbi tristique senectus et netus et malesuada fames ac turpis egestas. Fusce quam ex, commodo vitae pellentesque sit amet, tempor sodales purus.</p>
    <p>Suspendisse in sollicitudin mauris, in commodo dui. Aenean ut dui aliquam, elementum dolor vitae, commodo ex. Phasellus commodo enim ut fringilla commodo. Nulla porttitor erat at lacus interdum, et dictum enim sagittis. Morbi vel lacus sed dui elementum elementum in at turpis.</p>
    <p>Duis venenatis tristique lacus non porttitor. Aenean elit justo, molestie vel pretium nec, fringilla vitae augue. Etiam purus leo, faucibus ac varius in, tempor vel ex.</p>
  </div>
  <div class="bullets" style="left:268px;top:52px;width:205px">
    <p>Lorem ipsum dolor sit amet, consectetur adipiscing elit. Nulla sit amet urna sagittis, maximus orci eget, sodales nibh. Duis eu purus gravida, dignissim eros posuere, ornare nisi. Pellentesque habitant morbi tristique senectus et netus et malesuada fames ac turpis egestas. Fusce quam ex, commodo vitae pellentesque sit amet, tempor sodales purus.</p>
    <p>Suspendisse in sollicitudin mauris, in commodo dui. Aenean ut dui aliquam, elementum dolor vitae, commodo ex. Phasellus commodo enim ut fringilla commodo. Nulla porttitor erat at lacus interdum, et dictum enim sagittis. Morbi vel lacus sed dui elementum elementum in at turpis.</p>
    <p>Duis venenatis tristique lacus non porttitor. Aenean elit justo, molestie vel pretium nec, fringilla vitae augue. Etiam purus leo, faucibus ac varius in, tempor vel ex.</p>
  </div>
</section>

<!-- 20 Two topics -->
<section class="slide" style="left:906px;top:808px">
  <div class="rail"><span class="dot"></span><span class="url">www.vierklang-beratung.de</span><span class="num">20</span></div>
  <div class="title center" style="top:18px;font-size:17px">Two Topics Text Slide</div>
  <div style="left:40px;top:44px;width:212px;height:36px;background:var(--teal-mist);color:var(--gold);font-size:8px;text-align:center;line-height:1.25;padding-top:5px">Lorem ipsum dolor sit amet,<br>consectetur adipiscing elit</div>
  <div style="left:262px;top:44px;width:212px;height:36px;background:var(--teal-mist);color:var(--gold);font-size:8px;text-align:center;line-height:1.25;padding-top:5px">Lorem ipsum dolor sit amet,<br>consectetur adipiscing elit</div>
  <div class="bullets" style="left:44px;top:92px;width:204px">
    <p>Lorem ipsum dolor sit amet, consectetur adipiscing elit. Nulla sit amet urna sagittis, maximus orci eget, sodales nibh. Duis eu purus gravida, dignissim eros posuere, ornare nisi. Pellentesque habitant morbi tristique senectus et netus et malesuada fames ac turpis egestas. Fusce quam ex, commodo vitae pellentesque sit amet, tempor sodales purus.</p>
    <p>Suspendisse in sollicitudin mauris, in commodo dui. Aenean ut dui aliquam, elementum dolor vitae, commodo ex. Phasellus commodo enim ut fringilla commodo. Nulla porttitor erat at lacus interdum, et dictum enim sagittis.</p>
  </div>
  <div class="bullets" style="left:266px;top:92px;width:204px">
    <p>Lorem ipsum dolor sit amet, consectetur adipiscing elit. Nulla sit amet urna sagittis, maximus orci eget, sodales nibh. Duis eu purus gravida, dignissim eros posuere, ornare nisi. Pellentesque habitant morbi tristique senectus et netus et malesuada fames ac turpis egestas. Fusce quam ex, commodo vitae pellentesque sit amet, tempor sodales purus.</p>
    <p>Suspendisse in sollicitudin mauris, in commodo dui. Aenean ut dui aliquam, elementum dolor vitae, commodo ex. Phasellus commodo enim ut fringilla commodo. Nulla porttitor erat at lacus interdum, et dictum enim sagittis.</p>
  </div>
</section>

<!-- 21 Column chart -->
<section class="slide" style="left:33.5px;top:995px">
  <div class="rail"><span class="dot"></span><span class="url">www.vierklang-beratung.de</span><span class="num">21</span></div>
  <div class="title" style="left:36px;top:46px;font-size:12px;width:170px">Click to include your title slide for data analysis</div>
  <div class="bullets" style="left:36px;top:84px;width:170px">
    <p>Lorem ipsum dolor sit amet, consectetur adipiscing elit. Nulla sit amet urna sagittis, maximus orci eget, sodales nibh.</p>
    <p>Duis eu purus gravida, dignissim eros posuere, ornare nisi. Pellentesque habitant morbi tristique senectus et netus et malesuada fames ac turpis egestas.</p>
    <p>Fusce quam ex, commodo vitae pellentesque sit amet, tempor sodales purus. Cras convallis vestibulum urna nec convallis.</p>
    <p>Fusce eu auctor odio. Sed sagittis, libero ut pretium mollis, est eros maximus quam, nec ultrices ex diam eget ipsum.</p>
  </div>
  <svg style="left:0;top:0" width="516" height="290" viewBox="0 0 516 290" font-family="Jost, sans-serif">
    <text x="360" y="56" font-size="7" fill="#555" text-anchor="middle">Chart Title</text>
    <path d="M226 70 V234 H500" fill="none" stroke="#ddd" stroke-width=".8"/>
    <g>
      <rect x="238" y="146" width="9" height="88" fill="#00695c"/><rect x="249" y="178" width="9" height="56" fill="#6b6b6b"/><rect x="260" y="188" width="9" height="46" fill="#00BBA5"/>
      <rect x="300" y="168" width="9" height="66" fill="#00695c"/><rect x="311" y="110" width="9" height="124" fill="#6b6b6b"/><rect x="322" y="188" width="9" height="46" fill="#00BBA5"/>
      <rect x="362" y="140" width="9" height="94" fill="#00695c"/><rect x="373" y="190" width="9" height="44" fill="#6b6b6b"/><rect x="384" y="174" width="9" height="60" fill="#00BBA5"/>
      <rect x="424" y="104" width="9" height="130" fill="#00695c"/><rect x="435" y="160" width="9" height="74" fill="#6b6b6b"/><rect x="446" y="92" width="9" height="142" fill="#00BBA5"/>
    </g>
    <g font-size="4" fill="#999" text-anchor="middle">
      <text x="253" y="242">Category 1</text><text x="315" y="242">Category 2</text><text x="377" y="242">Category 3</text><text x="439" y="242">Category 4</text>
    </g>
    <g font-size="4" fill="#999">
      <rect x="322" y="249" width="4" height="4" fill="#00695c"/><text x="328" y="253">Series 1</text>
      <rect x="348" y="249" width="4" height="4" fill="#6b6b6b"/><text x="354" y="253">Series 2</text>
      <rect x="374" y="249" width="4" height="4" fill="#00BBA5"/><text x="380" y="253">Series 3</text>
    </g>
  </svg>
</section>

<!-- 22 Pie chart -->
<section class="slide" style="left:325px;top:995px">
  <div class="rail"><span class="dot"></span><span class="url">www.vierklang-beratung.de</span><span class="num">22</span></div>
  <div class="title" style="left:36px;top:46px;font-size:12px;width:170px">Click to include your title slide for data analysis</div>
  <div class="bullets" style="left:36px;top:84px;width:170px">
    <p>Lorem ipsum dolor sit amet, consectetur adipiscing elit. Nulla sit amet urna sagittis, maximus orci eget, sodales nibh.</p>
    <p>Duis eu purus gravida, dignissim eros posuere, ornare nisi. Pellentesque habitant morbi tristique senectus et netus et malesuada fames ac turpis egestas.</p>
    <p>Fusce quam ex, commodo vitae pellentesque sit amet, tempor sodales purus. Cras convallis vestibulum urna nec convallis.</p>
    <p>Fusce eu auctor odio. Sed sagittis, libero ut pretium mollis, est eros maximus quam, nec ultrices ex diam eget ipsum.</p>
  </div>
  <svg style="left:0;top:0" width="516" height="290" viewBox="0 0 516 290" font-family="Jost, sans-serif">
    <text x="338" y="56" font-size="7" fill="#555" text-anchor="middle">Sales</text>
    <path d="M218 150 L218 168 A120 62 0 0 0 458 168 L458 150 A120 62 0 0 1 218 150 Z" fill="#004d44"/>
    <path d="M338 150 L338 88 A120 62 0 1 1 267.4 200.2 Z" fill="#00897a"/>
    <path d="M338 150 L267.4 200.2 A120 62 0 0 1 233 119.9 Z" fill="#5f6660"/>
    <path d="M338 150 L233 119.9 A120 62 0 0 1 287.2 93.8 Z" fill="#00BBA5"/>
    <path d="M338 150 L287.2 93.8 A120 62 0 0 1 338 88 Z" fill="#67D7C9"/>
    <g font-size="4" fill="#999">
      <rect x="286" y="248" width="4" height="4" fill="#00897a"/><text x="292" y="252">1st Qtr</text>
      <rect x="310" y="248" width="4" height="4" fill="#5f6660"/><text x="316" y="252">2nd Qtr</text>
      <rect x="336" y="248" width="4" height="4" fill="#00BBA5"/><text x="342" y="252">3rd Qtr</text>
      <rect x="360" y="248" width="4" height="4" fill="#67D7C9"/><text x="366" y="252">4th Qtr</text>
    </g>
  </svg>
</section>

<!-- 23 Bar chart -->
<section class="slide" style="left:613px;top:995px">
  <div class="rail"><span class="dot"></span><span class="url">www.vierklang-beratung.de</span><span class="num">23</span></div>
  <div class="title" style="left:36px;top:46px;font-size:12px;width:170px">Click to include your title slide for data analysis</div>
  <div class="bullets" style="left:36px;top:84px;width:170px">
    <p>Lorem ipsum dolor sit amet, consectetur adipiscing elit. Nulla sit amet urna sagittis, maximus orci eget, sodales nibh.</p>
    <p>Duis eu purus gravida, dignissim eros posuere, ornare nisi. Pellentesque habitant morbi tristique senectus et netus et malesuada fames ac turpis egestas.</p>
    <p>Fusce quam ex, commodo vitae pellentesque sit amet, tempor sodales purus. Cras convallis vestibulum urna nec convallis.</p>
    <p>Fusce eu auctor odio. Sed sagittis, libero ut pretium mollis, est eros maximus quam, nec ultrices ex diam eget ipsum.</p>
  </div>
  <svg style="left:0;top:0" width="516" height="290" viewBox="0 0 516 290" font-family="Jost, sans-serif">
    <text x="350" y="56" font-size="7" fill="#555" text-anchor="middle">Sales</text>
    <path d="M242 64 V222" stroke="#ddd" stroke-width=".8"/>
    <g stroke="#eee" stroke-width=".6"><path d="M282 64V222M322 64V222M362 64V222M402 64V222M442 64V222M482 64V222"/></g>
    <g fill="#00897a">
      <rect x="242" y="70" width="30" height="20"/>
      <rect x="242" y="110" width="38" height="20"/>
      <rect x="242" y="150" width="98" height="20"/>
      <rect x="242" y="190" width="214" height="20" stroke="#67D7C9" stroke-width="1.5"/>
    </g>
    <g font-size="4" fill="#999" text-anchor="end">
      <text x="237" y="82">4th Qtr</text><text x="237" y="122">3rd Qtr</text><text x="237" y="162">2nd Qtr</text><text x="237" y="202">1st Qtr</text>
    </g>
    <g font-size="4" fill="#999">
      <rect x="300" y="246" width="4" height="4" fill="#00897a"/><text x="306" y="250">1st Qtr</text>
      <rect x="324" y="246" width="4" height="4" fill="#00897a"/><text x="330" y="250">2nd Qtr</text>
      <rect x="350" y="246" width="4" height="4" fill="#00897a"/><text x="356" y="250">3rd Qtr</text>
      <rect x="374" y="246" width="4" height="4" fill="#00897a"/><text x="380" y="250">4th Qtr</text>
    </g>
  </svg>
</section>

<!-- 24 Thank you -->
<section class="slide" style="left:906px;top:995px">
  <div class="ph" style="left:0;top:27px;width:488px;height:236px;background:linear-gradient(170deg,#ee7256 0%,#e8603f 50%,#d9533a 100%)" role="img" aria-label="Coral-toned mountain landscape photograph"></div>
  <div style="left:54px;top:78px;font-size:26px;font-weight:300;color:#fff">THANK YOU.</div>
  <div style="left:54px;top:122px;font-size:7px;color:#fde0d6">Vierklang Beratung GmbH</div>
  <div style="left:54px;top:138px;width:145px;height:1.5px;background:linear-gradient(90deg,var(--teal-soft),var(--gold))"></div>
  <div style="left:54px;top:154px;font-size:5px;color:#fde0d6;line-height:1.6;letter-spacing:.3px">Nachhaltigkeitsberatung<br>Sitz: Office Center Vierklang<br>Lindenweg 12<br>60311 Frankfurt a.M.<br>Tel.: +49 069 555 0123<br>E-Mail: info@vierklang-beratung.de</div>
  <div class="footer">Visit us | www.vierklang-beratung.de</div>
</section>

</div>
</body>
</html>
```